Redesign Of Current Landing Page

I need to redesign this landing page https://www.brightlanepromo.biz/?page=landing&landing=23 (Please do not opt in because when you do it will show you the home page. Please clear your cookies before going to this url above to view the 1 page landing page.)

Please use my updated website as a reference for colors and logo.
http://sitecradlewerk.com/dh/bpq/index.html

I would like the call to action to be a button that opens into a lead form...

Button would be "Download Samples"

Target Market(s)

small business owners

Industry/Entity Type

Marketing

Number of Pages Required

1 page

Colors

Designer to choose colors to be used in the design.

Requirements
Must have
• must be full responsive on all devices
Nice to have
• must have a legitimate professional apeal to it
Should not have
• open

```html
<!DOCTYPE html>
<html lang="en">
<head>
<meta charset="utf-8">
<title>Brightlane Promo Group – Incentives</title>
<link href="https://fonts.googleapis.com/css2?family=Lato:wght@400;700;900&display=swap" rel="stylesheet">
<style>
:root{
  --blue:#1d6fb8;
  --orange:#f9a61a;
  --ink:#333;
  --muted:#555;
  --light:#f0f0f0;
  --footer:#d4d4d4;
  --white:#fff;
}
*{box-sizing:border-box;margin:0;padding:0}
html,body{width:1200px;height:3025px;overflow:hidden}
body{font-family:'Lato',sans-serif;color:var(--ink);background:var(--white);position:relative}
section,header,footer{position:absolute;left:0;width:1200px}
.btn{position:absolute;display:flex;align-items:center;justify-content:center;text-align:center;white-space:nowrap;background:var(--orange);color:#222;font-weight:700;font-size:17px;letter-spacing:.1px;height:56px;width:448px;text-transform:uppercase;text-decoration:none}
.btn-center{left:376px}

/* hero */
.hero{top:0;height:660px}
.hero-photo{position:absolute;inset:0;background:linear-gradient(180deg,#f3e6cf 0%,#e9d6b6 28%,#8fb8b9 50%,#2f8f9a 68%,#c9b89a 100%)}
.topbar{position:absolute;top:0;left:0;width:1200px;height:90px}
.brand{position:absolute;left:130px;top:34px;display:flex;align-items:center;gap:10px;font-weight:900;font-size:30px;color:#1b3d6e}
.brand-dot{width:28px;height:28px;border-radius:50%;background:var(--blue)}
.contact{position:absolute;top:20px;font-weight:700;font-size:17px;color:#222;display:flex;align-items:center;gap:10px}
.contact .ic{width:22px;height:22px;border-radius:50%;background:var(--orange);display:flex;align-items:center;justify-content:center}
.hero-card{position:absolute;left:323px;top:186px;width:557px;height:350px;background:rgba(70,70,70,.72);border:2px solid rgba(255,255,255,.35);text-align:center;color:var(--white)}
.hero-card h1{font-weight:900;font-size:40px;line-height:48px;margin-top:28px}
.hero-card .sub{font-size:24px;line-height:28px;margin-top:10px}
.hero-card .note{font-size:15px;line-height:20px;margin-top:14px}
.hero-card .btn{left:46px;top:262px;width:462px}

/* imagine */
.imagine{top:660px;height:607px;background:var(--light)}
.section-title{font-weight:900;font-size:31px;color:var(--blue);text-transform:uppercase}
.imagine .section-title{position:absolute;left:131px;top:66px}
.imagine-box{position:absolute;left:131px;top:127px;width:635px;height:303px;border:1px solid #ddd;background:#f6f6f6;padding:36px 40px 0 40px;font-size:14.5px;line-height:20px;color:var(--ink)}
.imagine-box p{margin-bottom:18px;max-width:520px}
.samples{position:absolute;left:700px;top:117px;width:360px;height:333px;background:linear-gradient(135deg,#2c4f9a,#3a2b5c 55%,#c58a2c);border-radius:4px}
.imagine .btn{left:131px;top:460px}

/* how */
.how{top:1267px;height:468px}
.how-photo{position:absolute;inset:0;background:linear-gradient(180deg,#4a8fc4 0%,#2f84c9 45%,#1e7fca 100%)}
.how .section-title{position:absolute;width:100%;top:60px;text-align:center;color:var(--orange)}
.how-text{position:absolute;left:250px;width:700px;text-align:center;color:var(--white);font-size:14.5px;line-height:21px}
.how .btn{top:347px}

/* why */
.why{top:1735px;height:645px;background:var(--white)}
.why .section-title{position:absolute;width:100%;top:86px;text-align:center;line-height:41px}
.icon{position:absolute;top:232px;width:134px;height:134px;border:2px solid var(--blue);border-radius:50%;display:flex;align-items:center;justify-content:center}
.icon-label{position:absolute;top:406px;width:200px;text-align:center;font-size:13.5px;line-height:20px;color:#222}
.why .btn{top:500px}

/* testimonials */
.testimonials{top:2380px;height:582px;background:var(--light)}
.testimonials .section-title{position:absolute;width:100%;top:72px;text-align:center}
.quote-mark{position:absolute;font-size:64px;font-weight:900;color:#333;line-height:1}
.quote{position:absolute;left:320px;top:150px;width:560px;text-align:center;font-size:14px;line-height:28px;color:var(--muted)}
.author{position:absolute;width:100%;top:350px;text-align:center;font-size:11px;font-weight:700;color:var(--blue)}
.place{position:absolute;width:100%;top:370px;text-align:center;font-size:11px;color:var(--muted)}
.testimonials .btn{top:456px}

footer{top:2962px;height:63px;background:var(--footer);display:flex;align-items:center;justify-content:center;font-size:11px;color:#555}
</style>
</head>
<body>

<header class="hero">
  <div class="hero-photo" role="img" aria-label="Family walking along a sunny beach at the water's edge"></div>
  <div class="topbar">
    <div class="brand"><span class="brand-dot"></span>Brightlane</div>
    <div class="contact" style="left:678px">
      <span class="ic"><svg width="12" height="12" viewBox="0 0 24 24"><path d="M6.6 10.8a15 15 0 0 0 6.6 6.6l2.2-2.2c.3-.3.7-.4 1-.2 1.1.4 2.3.6 3.6.6.6 0 1 .4 1 1V20c0 .6-.4 1-1 1A17 17 0 0 1 3 4c0-.6.4-1 1-1h3.5c.6 0 1 .4 1 1 0 1.3.2 2.5.6 3.6.1.3 0 .7-.2 1z" fill="#222"/></svg></span>1-800-555-0142</div>
    <div class="contact" style="left:858px">
      <span class="ic"><svg width="12" height="12" viewBox="0 0 24 24"><circle cx="12" cy="12" r="9" fill="none" stroke="#222" stroke-width="3"/><path d="M12 7v5l3 2" stroke="#222" stroke-width="3" fill="none"/></svg></span>MON-FRI 8AM-5PM PST</div>
  </div>
  <div class="hero-card">
    <h1>ATTRACT MORE<br>CUSTOMERS</h1>
    <p class="sub">who spend more money with your<br>business more often!</p>
    <p class="note">Using Free Vacation &amp; Cruise Certificates And Other<br>Incentives Without Breaking The Bank!</p>
    <a class="btn">Download Free Samples Of Our Incentives</a>
  </div>
</header>

<section class="imagine">
  <h2 class="section-title">Imagine</h2>
  <div class="imagine-box">
    <p>Being able to create exciting give away promotions that will boost your sales without ever having to worry about cost.</p>
    <p>Brightlane Promo Group, Inc. provides high-perceived value promotional incentives to businesses that want to advertise an exciting Give Away that will instantly attract more customers from your existing advertising efforts.</p>
    <p>Your business can give away incentive certificates that are redeemable for luxury hotel &amp; resort stays with airfare included, cruises, cash for gas, groceries, dining and even electronic goods.</p>
  </div>
  <div class="samples" role="img" aria-label="Fanned stack of sample incentive certificates for travel, cash back and electronics"></div>
  <a class="btn">Download Free Samples Of Our Incentives</a>
</section>

<section class="how">
  <div class="how-photo" role="img" aria-label="Tropical resort with palm trees and overwater bungalow in blue tint"></div>
  <h2 class="section-title">How Can We Do It?</h2>
  <p class="how-text" style="top:120px">We help fill empty rooms for thousands of hotels and resorts in hundreds of destinations around the world as well as the major cruise lines. Hotels and resorts are rarely full so when we place someone in their empty rooms, they end up making it up when travelers spend money on room service, spa services, eat at their in-house restaurants, casino and take advantage of other amenities that drive revenue.</p>
  <p class="how-text" style="top:237px">We also help over 18,000 restaurants, electronic manufacturers, the major gas companies and top grocery chains in the U.S and Canada increase brand awareness as well as increase customer loyalty.</p>
  <a class="btn btn-center">Download Free Samples Of Our Incentives</a>
</section>

<section class="why">
  <h2 class="section-title">Why Offer Incentives<br>To Customers?</h2>

  <div class="icon" style="left:127px"><svg width="64" height="56" viewBox="0 0 64 56" fill="none" stroke="#1d6fb8" stroke-width="3"><path d="M4 2v50h58"/><rect x="14" y="34" width="7" height="16" fill="#1d6fb8"/><rect x="26" y="26" width="7" height="24" fill="#1d6fb8"/><rect x="38" y="30" width="7" height="20" fill="#1d6fb8"/><rect x="50" y="18" width="7" height="32" fill="#1d6fb8"/><path d="M12 28l14-12 10 8 18-16"/><path d="M48 8h6v6"/></svg></div>
  <div class="icon-label" style="left:94px">Increase Responses<br>From Your Existing Ads</div>

  <div class="icon" style="left:288px"><svg width="64" height="56" viewBox="0 0 64 56" fill="#1d6fb8"><circle cx="24" cy="22" r="13"/><g stroke="#1d6fb8" stroke-width="6"><path d="M24 4v36M6 22h36M11 9l26 26M37 9L11 35"/></g><circle cx="24" cy="22" r="5" fill="#fff"/><circle cx="48" cy="40" r="9"/><g stroke="#1d6fb8" stroke-width="4"><path d="M48 28v24M36 40h24M40 32l16 16M56 32L40 48"/></g><circle cx="48" cy="40" r="3.5" fill="#fff"/></svg></div>
  <div class="icon-label" style="left:255px">#1 Sales Closing Tool -<br>Gift w/ Purchase</div>

  <div class="icon" style="left:447px"><svg width="50" height="64" viewBox="0 0 50 64" fill="#1d6fb8"><path d="M12 34L4 58l10-4 6 8 6-20z"/><path d="M38 34l8 24-10-4-6 8-6-20z"/><circle cx="25" cy="22" r="20"/><circle cx="25" cy="22" r="13" fill="#fff"/><path d="M25 13l3 6 6 1-4.5 4 1 6-5.5-3-5.5 3 1-6L16 20l6-1z"/></svg></div>
  <div class="icon-label" style="left:414px">Build Brand<br>Awareness and Trust</div>

  <div class="icon" style="left:615px"><svg width="64" height="56" viewBox="0 0 64 56" fill="#1d6fb8"><path d="M32 4l13 5v10c0 9-6 15-13 18-7-3-13-9-13-18V9z"/><path d="M27 20l4 4 7-8" stroke="#fff" stroke-width="3" fill="none"/><path d="M2 26h6l10 14h12v6H14L2 34z"/><path d="M62 26h-6L46 40H34v6h16l12-12z"/></svg></div>
  <div class="icon-label" style="left:582px">Insure The Sale Over<br>Your Competition</div>

  <div class="icon" style="left:782px"><svg width="66" height="46" viewBox="0 0 66 46" fill="#1d6fb8"><path d="M0 8h10l2 22H0z"/><path d="M66 8H56l-2 22h12z"/><path d="M12 12l14-6 8 4 8-4 12 6v16l-18 14c-2 1-4 1-5 0L12 28z"/><path d="M30 12l-8 8c2 2 5 2 7 0l5-4 12 12" stroke="#fff" stroke-width="2.5" fill="none"/></svg></div>
  <div class="icon-label" style="left:749px">Boost Repeat and<br>Referral Business-</div>

  <div class="icon" style="left:943px"><svg width="60" height="60" viewBox="0 0 60 60" fill="none" stroke="#1d6fb8" stroke-width="4"><path d="M10 22A22 22 0 0 1 48 14"/><path d="M50 38A22 22 0 0 1 12 46"/><path d="M48 4v10H38"/><path d="M12 56V46h10"/><circle cx="30" cy="30" r="12" stroke-width="2.5"/><text x="30" y="36" text-anchor="middle" font-family="Lato,sans-serif" font-size="17" font-weight="900" fill="#1d6fb8" stroke="none">$</text></svg></div>
  <div class="icon-label" style="left:910px">Improve<br>Retention Rates</div>

  <a class="btn btn-center">Download Free Samples Of Our Incentives</a>
</section>

<section class="testimonials">
  <h2 class="section-title">Testimonials</h2>
  <span class="quote-mark" style="left:288px;top:132px">&ldquo;</span>
  <p class="quote">I began using your incentives two years ago to boost lead generation efforts. I have experienced a 63% increase in lead captures. And, even more importantly, my sales have increased as well. The ability to offer unlimited certificates and not having to pay for each certificate I give away is perhaps the best feature of the program, but having the flexibility to email or print certificates for my customers is also wonderful. I even use your html banners to automate my promotions right on my website!.</p>
  <span class="quote-mark" style="left:790px;top:312px">&rdquo;</span>
  <p class="author">Dana R.</p>
  <p class="place">Greenfield, TN</p>
  <a class="btn btn-center">Download Free Samples Of Our Incentives</a>
</section>

<footer>© 2017 Brightlane Promo Group, Inc. - All Rights Reserved</footer>

</body>
</html>
```